Modern Verdell Tree Care Website

I need a website for a full service Tree Care company. The company provides tree pruning, tree removal, tree preservation, emergency services, stump grinding, and emergency tree services.

Target Market(s)

Customers that need tree services

Industry/Entity Type

Landscaping, Tree Services

Coding

Coded - Design and coding required

Number of Pages Required

5+ page

Font styles to use
Sans Serif

Requirements
Must have
• Good clean design that showcases the services the company provides.
Nice to have
• Services page; contact form, blog, home page, about page

```html
<!DOCTYPE html>
<html lang="en">
<head>
<meta charset="utf-8">
<title>Verdell Tree Care</title>
<link rel="stylesheet" href="https://fonts.googleapis.com/css2?family=Oswald:wght@500;600;700&family=Poppins:wght@400;500;600&display=swap">
<style>
:root{
  --orange:#f9ab36;
  --orange-deep:#f29a1f;
  --slate:#5b6670;
  --button-slate:#5f6c77;
  --ink:#333;
  --muted:#555;
  --white:#fff;
  --gold-line:#d7c46a;
  --forest:#3d4a1e;
}
*{box-sizing:border-box;margin:0;padding:0}
html,body{width:1200px;height:4263px;overflow:hidden}
body{position:relative;font-family:'Poppins',sans-serif;color:var(--ink);background:var(--white)}
.abs{position:absolute}
.display{font-family:'Oswald',sans-serif;font-weight:600;text-transform:uppercase;letter-spacing:.5px}
.btn{position:absolute;display:flex;align-items:center;justify-content:center;font-weight:500;text-transform:uppercase;color:var(--white);font-size:14px}
.btn-orange{background:var(--orange)}
.btn-slate{background:var(--button-slate)}
.photo{position:absolute}

/* header */
.site-header{position:absolute;left:0;top:0;width:1200px;height:80px;background:var(--white)}
.brand{position:absolute;display:flex;align-items:center;gap:12px;font-family:'Poppins',sans-serif;font-weight:600;color:var(--slate);white-space:nowrap}
.brand-mark{width:22px;height:22px;background:var(--orange);flex:none}
.nav a{position:absolute;top:31px;font-size:13px;color:var(--muted);text-decoration:none;text-transform:uppercase}
.nav a.active{color:var(--orange)}
.nav-indicator{position:absolute;left:627px;top:0;width:40px;height:3px;background:var(--orange)}

/* hero */
.hero{left:0;top:80px;width:1200px;height:638px;background:radial-gradient(ellipse at 45% 55%,#6b5a3a 0%,#4f5a2a 45%,#2f3b1a 100%)}
.hero-title{position:absolute;left:0;width:1200px;top:290px;text-align:center;color:var(--white);font-size:74px;line-height:74px}
.hero-sub{position:absolute;left:0;width:1200px;top:447px;text-align:center;color:var(--white);font-size:17px}

/* about */
.section-title{color:var(--slate);font-size:46px;line-height:1}
.about-text{position:absolute;left:202px;top:898px;width:420px;font-size:13.6px;line-height:21.5px;color:var(--muted)}
.about-text p+p{margin-top:16px}

/* services */
.service-card{position:absolute;top:1328px;width:318px;height:214px;border:3px solid var(--orange)}
.service-label{position:absolute;top:1550px;width:318px;text-align:center;color:var(--slate);font-size:28px}

/* why choose */
.why-list{position:absolute;left:129px;top:1948px;list-style:none;color:var(--white);font-size:14px;line-height:26.8px;font-weight:500}
.why-list li::before{content:"» ";color:var(--orange)}

/* testimonial */
.quote-text{position:absolute;left:601px;top:2420px;width:395px;font-size:18px;line-height:31px;color:var(--ink)}

/* contact */
.field{position:absolute;border:2px solid var(--gold-line);color:var(--white);font-size:16px;padding:14px 25px}

/* footer */
.foot-head{position:absolute;font-family:'Oswald',sans-serif;font-weight:600;color:var(--slate);font-size:17px;text-transform:uppercase}
.foot-list{position:absolute;list-style:none;font-size:13px;line-height:22.3px;color:var(--ink)}
.social{position:absolute;top:3992px;width:27px;height:27px;border-radius:50%;background:var(--orange)}
</style>
</head>
<body>

<header class="site-header">
  <div class="brand" style="left:205px;top:22px;font-size:26px;">
    <span class="brand-mark"></span>Verdell Tree Care
  </div>
  <nav class="nav">
    <span class="nav-indicator"></span>
    <a class="active" style="left:630px">Home</a>
    <a style="left:708px">Services</a>
    <a style="left:807px">About Us</a>
    <a style="left:910px">Contact Us</a>
  </nav>
</header>

<section class="photo hero" role="img" aria-label="Arborist in safety glasses working among leafy branches"></section>
<h1 class="hero-title display">Call Verdell for all<br>your tree care needs</h1>
<p class="hero-sub">Serving Marrowfield and surrounding areas</p>
<a class="btn btn-orange" style="left:503px;top:517px;width:194px;height:46px;">Get a free quote</a>

<h2 class="abs section-title display" style="left:202px;top:832px;">About Us</h2>
<div class="about-text">
  <p>At Verdell Tree Care, we are more than just a tree service company, we are stewards of our beautiful trees. With a passion deeply rooted in arboriculture, we embark on a mission to promote the health, beauty, and safety of your trees and landscapes.</p>
  <p>Whether it's expert tree trimming to enhance aesthetics, meticulous tree removal to mitigate hazards, or comprehensive tree health assessments to ensure safety, we approach each task with unwavering dedication and attention to detail.</p>
</div>
<div class="photo" style="left:683px;top:827px;width:312px;height:311px;background:linear-gradient(135deg,#6f8f3c,#c9d6b0 50%,#b54a3a)" role="img" aria-label="Arborist trimming a flowering tree, framed in a large letter shape"></div>

<h2 class="abs section-title display" style="left:0;width:1200px;text-align:center;top:1242px;">Tree Care Our Services</h2>
<div class="photo service-card" style="left:83px;background:linear-gradient(160deg,#8a6a3a,#4f7a2e 60%,#c9a24c)" role="img" aria-label="Worker pruning a shrub with loppers"></div>
<div class="photo service-card" style="left:438px;background:linear-gradient(160deg,#7da3d8,#6b5a44 55%,#8fb3e0)" role="img" aria-label="Worker cutting a tree trunk with a chainsaw"></div>
<div class="photo service-card" style="left:794px;background:linear-gradient(160deg,#4f6d8f,#6b7c52 50%,#9bb7dc)" role="img" aria-label="Chainsaw clearing felled tree sections"></div>
<h3 class="service-label display" style="left:83px;">Tree Trimming</h3>
<h3 class="service-label display" style="left:438px;">Tree Removal</h3>
<h3 class="service-label display" style="left:794px;">Tree Clearing</h3>
<a class="btn btn-orange" style="left:503px;top:1598px;width:194px;height:45px;">View all services</a>

<section class="photo" style="left:0;top:1742px;width:1200px;height:508px;background:linear-gradient(90deg,#2d3518 0%,#3f4a20 45%,#6d7a34 70%,#a6632a 100%)" role="img" aria-label="Arborist in orange cap pruning branches with long-handled shears"></section>
<div class="abs" style="left:218px;top:1845px;width:137px;height:3px;background:var(--orange)"></div>
<h2 class="abs display" style="left:129px;top:1887px;font-size:46px;color:var(--white);">Why Choose Us?</h2>
<ul class="why-list">
  <li>Licensed and Insured</li>
  <li>24-Hours Emergency Services</li>
  <li>Locally Owned &amp; Operated</li>
  <li>Professional Work</li>
  <li>Safety is Our No.1 Priority</li>
  <li>Free Estimates</li>
  <li>Licensed Arborist on Staff</li>
</ul>
<div class="abs" style="left:88px;top:1990px;width:3px;height:162px;background:var(--orange)"></div>
<div class="abs" style="left:88px;top:2149px;width:290px;height:3px;background:var(--orange)"></div>

<div class="abs" style="left:0;top:2375px;width:549px;height:547px;border:2px solid var(--gold-line);border-left:none"></div>
<div class="photo" style="left:0;top:2352px;width:507px;height:528px;background:linear-gradient(150deg,#5e4a6e,#6f7a34 40%,#3f4a1c)" role="img" aria-label="Hands cutting a branch with orange pruning shears"></div>
<p class="quote-text">There are many variations of passages of Lorem Ipsum available, but the majority have suffered alteration in some form, by injected humour, or randomised words which don't look even slightly believable. If you are going to use a passage of Lorem Ipsum, you need to be sure there isn't anything embarrassing hidden in the middle of text. All the Lorem Ipsum generators on the Internet tend to repeat predefined chunks as</p>
<p class="abs" style="left:601px;top:2808px;font-size:18px;">Lorem ipsum</p>
<svg class="abs" style="left:598px;top:2856px" width="70" height="20" viewBox="0 0 70 20" aria-hidden="true">
  <path d="M9 4 L3 10 L9 16" fill="none" stroke="#f9ab36" stroke-width="2"/>
  <path d="M59 4 L65 10 L59 16" fill="none" stroke="#f9ab36" stroke-width="2"/>
</svg>
<svg class="abs" style="left:968px;top:2688px" width="232" height="215" viewBox="0 0 232 215" aria-hidden="true">
  <g fill="#f9ab36">
    <path d="M55 10 C90 10 110 40 110 80 C110 140 70 190 15 210 L10 198 C45 180 65 150 68 125 C30 125 5 100 5 65 C5 30 28 10 55 10 Z"/>
    <path d="M175 10 C210 10 230 40 230 80 C230 140 190 190 135 210 L130 198 C165 180 185 150 188 125 C150 125 125 100 125 65 C125 30 148 10 175 10 Z"/>
  </g>
  <g fill="#fff"><path d="M40 28 C60 22 80 30 86 44 C70 36 55 34 40 38 Z"/><path d="M160 28 C180 22 200 30 206 44 C190 36 175 34 160 38 Z"/></g>
</svg>

<section class="photo" style="left:0;top:3030px;width:1200px;height:545px;background:linear-gradient(90deg,#2e3a19 0%,#3d4a1e 50%,#5d6a2c 70%,#3a3a22 100%)" role="img" aria-label="Arborist in high-visibility vest resting a hand on a tree trunk in a forest"></section>
<h2 class="abs display" style="left:87px;top:3110px;font-size:48px;color:var(--white);">Get In Touch</h2>
<div class="field" style="left:90px;top:3187px;width:255px;height:59px;">Your Name</div>
<div class="field" style="left:367px;top:3187px;width:257px;height:59px;">Email Address</div>
<div class="field" style="left:90px;top:3263px;width:255px;height:59px;">Phone Number</div>
<div class="field" style="left:367px;top:3263px;width:257px;height:59px;">Location</div>
<div class="field" style="left:90px;top:3340px;width:534px;height:98px;">Comment</div>
<a class="btn btn-slate" style="left:90px;top:3456px;width:150px;height:44px;">Submit now</a>

<section class="abs" style="left:86px;top:3680px;width:1024px;height:220px;background:var(--orange)"></section>
<h2 class="abs display" style="left:137px;top:3743px;font-size:37px;line-height:44px;color:var(--white);font-weight:500;">Call us today to see how we can help<br>you with all of your tree needs:</h2>
<a class="btn btn-slate" style="left:915px;top:3783px;width:149px;height:43px;font-size:12px;">Contact us</a>

<div class="brand" style="left:128px;top:3980px;font-size:23px;gap:12px;">
  <span class="brand-mark" style="width:36px;height:36px;"></span>Verdell Tree Care
</div>
<div class="foot-head" style="left:481px;top:3960px;">Home</div>
<ul class="foot-list" style="left:480px;top:3989px;">
  <li>Services</li><li>About Us</li><li>Contact us</li>
</ul>
<div class="foot-head" style="left:595px;top:3960px;">Tree Care Our Services</div>
<ul class="foot-list" style="left:595px;top:3986px;">
  <li>Tree Trimming</li><li>Tree Removal</li><li>Tree Clearing</li><li>Tree Pruning</li><li>Tree Preservation</li><li>Storm Damage Cleanup</li><li>Emergency Tree Services</li><li>Cabling &amp; Bracing</li><li>Stump Grinding</li>
</ul>
<div class="foot-head" style="left:819px;top:3960px;">Follow Up</div>
<span class="social" style="left:819px"></span>
<span class="social" style="left:853px"></span>
<span class="social" style="left:888px"></span>
<span class="social" style="left:923px"></span>
<p class="abs" style="left:819px;top:4068px;font-size:11px;color:#aaa;">Email Address</p>
<svg class="abs" style="left:1050px;top:4067px" width="16" height="16" viewBox="0 0 16 16" aria-hidden="true"><path d="M1 8 L15 2 L11 15 L8 9 Z" fill="#f9ab36"/></svg>
<div class="abs" style="left:819px;top:4091px;width:253px;height:1px;background:var(--orange)"></div>

<div class="abs" style="left:148px;top:4214px;width:903px;height:1px;background:#bbb"></div>
<p class="abs" style="left:0;width:1200px;text-align:center;top:4228px;font-size:13px;color:var(--ink);">© 2024 Verdell Tree Care. All Rights Reserved.</p>
<svg class="abs" style="left:1109px;top:4202px" width="42" height="42" viewBox="0 0 42 42" aria-hidden="true">
  <circle cx="21" cy="21" r="20" fill="#f9ab36"/>
  <path d="M21 28 V14 M15 20 L21 14 L27 20" fill="none" stroke="#fff" stroke-width="2"/>
</svg>

</body>
</html>
```